tinyTally Resource Book - 10 maths tasks to do outside

I need a 22 (11 pages back to back) page A6 sized book produced to standard for submission to professional printer. Needs to be as .pdf file showing guide lines and allowances for colour bleed. I have text already written and submitted as attachment in a Word file with margins set to A6 size. The theme of the materials is "Nature Play" so using lots of pictures from nature (Australia preferably) and showing lots of patterns in nature (rocks, leaves, flower petals etc). Some of the tasks refer to specific activities, such as "shadows" and "floating" so would be great to illustrate appropriately. The big emphasis is on learning outside the classroom, getting kids to engage actively with nature. I would like to see the pages as full colour - so not white background. The book itself will be spiral bound along the top edge so a margin of at least 1cm will be required at the top of each page (or the bottom of even numbered pages). Book will be printed on plastic laminated matte paper for outdoor use. Font size needs to be big enough to read. Fonts sizes, alignments and page numbers are all different at the moment and need to be standardised. One photo is included in a page as a sample if you can use it, otherwise disregard. Logo for Wattlebrook Numeracy Guild is also included to have as part of the acknowledgements at the back of the book.

Target Market(s)

Book is for early childhood and preschool teachers.

Industry/Entity Type

Education

Font styles to use
Sans Serif

Requirements
Must have
• Colour and appeal.
Nice to have
• Use of natural colours instead of bright catchy colours but that is your call.
Should not have
• American spelling

```html
<!DOCTYPE html>
<html lang="en-AU">
<head>
<meta charset="utf-8">
<title>tinyTally – 7. Make a Star</title>
<link rel="stylesheet" href="https://fonts.googleapis.com/css2?family=Mulish:wght@900&family=Didact+Gothic&display=swap">
<style>
  :root {
    --paper: #ffffff;
    --trim-line: #222222;
    --sky-top: #8fc3d6;
    --sea: #b9d4dc;
    --mist: #d9dcd8;
    --pebble-light: #e6ddd0;
    --pebble-mid: #cbbfae;
    --pebble-dark: #a89a88;
    --heading: #2c3a8e;
    --heading-edge: #ffffff;
    --body-text: #3a3530;
    --bullet: #d62a2a;
    --deck-wood: #6d5a4a;
    --deck-stone: #b79a82;
  }
  * { box-sizing: border-box; margin: 0; padding: 0; }
  html, body { width: 902px; height: 1200px; overflow: hidden; background: var(--paper); }
  .page { position: relative; width: 902px; height: 1200px; background: var(--paper); }
  .trim-marks { position: absolute; inset: 0; }
  .bleed-area {
    position: absolute; left: 54px; top: 52px; width: 796px; height: 1096px;
    background: linear-gradient(180deg,
      var(--sky-top) 0%, var(--sea) 12%, var(--mist) 24%,
      var(--pebble-light) 38%, var(--pebble-mid) 70%, var(--pebble-dark) 100%);
  }
  .content { position: absolute; inset: 0; font-family: "Didact Gothic", "Century Gothic", sans-serif; color: var(--body-text); }
  .task-title, .section-heading {
    position: absolute; left: 126px;
    font-family: "Mulish", "Century Gothic", sans-serif; font-weight: 900;
    color: var(--heading);
    -webkit-text-stroke: 1px var(--heading-edge);
    paint-order: stroke fill;
    text-shadow: 2px 2px 0 var(--heading-edge), -1px -1px 0 var(--heading-edge), 1px -1px 0 var(--heading-edge), -1px 1px 0 var(--heading-edge), 3px 3px 4px rgba(0,0,0,.35);
    white-space: nowrap;
  }
  .task-title { top: 140px; font-size: 48px; letter-spacing: 0.5px; }
  .section-heading { font-size: 36px; }
  .points { position: absolute; left: 186px; list-style: none; font-size: 26px; line-height: 36px; }
  .points li { position: relative; padding-left: 34px; }
  .points li::before {
    content: ""; position: absolute; left: 2px; top: 10px; width: 15px; height: 15px;
    background: var(--bullet); transform: rotate(45deg);
  }
  .activity-photo {
    position: absolute; left: 516px; top: 730px; width: 262px; height: 362px;
    background: linear-gradient(170deg, var(--deck-stone) 0%, var(--deck-wood) 35%, #5a4a3d 100%);
    box-shadow: 2px 3px 6px rgba(0,0,0,.3);
  }
</style>
</head>
<body>
<div class="page">
  <div class="bleed-area" role="img" aria-label="Close-up photo of smooth beach pebbles with the sea and sky behind"></div>

  <svg class="trim-marks" width="902" height="1200" viewBox="0 0 902 1200" aria-hidden="true">
    <g stroke="var(--trim-line)" stroke-width="1" fill="none">
      <path d="M54 0V40M76 36V76M0 54H40M36 76H76"/>
      <path d="M848 0V40M826 36V76M902 54H862M866 76H826"/>
      <path d="M54 1200V1160M76 1164V1124M0 1146H40M36 1124H76"/>
      <path d="M848 1200V1160M826 1164V1124M902 1146H862M866 1124H826"/>
    </g>
  </svg>

  <div class="content">
    <h1 class="task-title">7. Make a Star</h1>
    <ul class="points" style="top:192px">
      <li>Put down a number of objects in a cir-<br>cle or bunch</li>
      <li>Partner puts down a corresponding ob-<br>ject on the outside of the circle, one for<br>each original object</li>
      <li>Keep adding objects to each arm of the<br>star as it grows</li>
    </ul>

    <h2 class="section-heading" style="top:452px">Prompting questions</h2>
    <ul class="points" style="top:496px">
      <li>How big can you make the star?</li>
      <li>Does each arm of the star need to have<br>the same number of objects?</li>
    </ul>

    <h2 class="section-heading" style="top:612px">Variations</h2>
    <ul class="points" style="top:656px">
      <li>Start with different numbers of objects –<br>3 (triangle), 4 (square) etc and compare<br>the resulting stars</li>
      <li>Use combinations<br>of different materials<br>to grow star</li>
    </ul>

    <h2 class="section-heading" style="top:882px">Big Ideas</h2>
    <ul class="points" style="top:926px">
      <li>Repeated addition</li>
      <li>Symmetry</li>
      <li>Growing patterns</li>
      <li>Decreasing patterns</li>
    </ul>

    <div class="activity-photo" role="img" aria-label="Photo of a child in a sun hat arranging rocks into a star shape on a timber deck"></div>
  </div>
</div>
</body>
</html>
```